Wordpress Theme for Medical Clinics

** Please view updated Sitemap2.pdf doc to clarify some confusion ***

This is a multiuser WordPress subscription site for medical clinics. Please see attachment for sitemap. Please do not include extra content like social media icons, search bars, or images. If you have questions, please ask for clarification.
The site contains the following pages and sub-pages:

1. Home
2. Our Clinic
2a. Our Clinic > Mission
2b. Our Clinic > Services
2c. Our Clinic > Clinic Policies
2d. Our Clinic > Schedules
3. Our Staff
3a. Our Staff > [Staff member page]
4. Resources
4a. Resources > Patient Health (index)
4b. Resources > Patient Health (index) > [post]
4c. Resources > Links
4d. Resources > Forms
5. Alerts
5a. Alerts > [Alert Page]
6. Contact Us

Includes the Following Pages, Subpages, and Content
1. Home
a. About Us
b. Our Staff
c. Bulletins
d. Accepting New Patients (shown as an alert widget)
e. Links
i. Physician Toolbox
ii. Book an Appointment
f. Clinic Policies
i. Show first 3 policies (e.g. Late Arrivals, Missed Appointments, Fees)
ii. Link to Clinic Policies page
g. Primary widget (displayed on all pages)
i. Hours of operation
ii. Contact Info
1. Tel
2. Fax
3. Email
4. Address
5. Get directions (link to Google Maps)
2. Our Clinic
a. Main Page
i. Clinic Name
ii. Overview
iii. Languages Spoken
iv. Secondary Navigation
1. Mission
2. Services
3. Clinic Policies
4. Schedules (see attachment)
b. Our Clinic > Mission
c. Our Clinic > Services
i. For each service include service TITLE and DESCRIPTION
d. Our Clinic > Clinic Policies
i. For each policy include policy TITLE and DESCRIPTION
ii. Include the following policies in mockup
1. Late arrivals
2. Missed appointments
3. Fees for missed appointments
4. Referrals and follow-ups
5. Services not covered by RDA
6. Information for LTF patients
7. Medical Legal Reports
e. Our Clinic > Schedules
3. Our Staff
a. Main Page
i. Display a list of staff members. Include NAME and DESIGNATION
b. Our Staff > [Staff Name]
i. Include NAME, PICTURE, DESIGNATION, and BIO
4. Resources
a. Resources > Patient Health
i. Main Page
1. Posts (ordered by date)
a. Title
b. Summary
2. Side Navigation
a. Post Categories
ii. Patient Health > [post title]
1. Title
2. Post Category
3. Date
4. Author
5. Summary
6. Body
b. Resources > Links
1. Secondary Navigation - Categories
a. Sample Categories:
i. Local Services
ii. RDA and Drug Coverage
iii. Mental Health Resources
2. Category page
a. Include the following links in the 'Local Services' category
i. Hypertension clinics
ii. Home Care services
iii. Vaccine Clinics
c. Resources > Forms
i. Display a table with form TITLE and CATEGORY
ii. Side Navigation
1. Form Categories
a. Use the following sample Categories
i. Referrals
ii. Insurance
iii. Intake
iv. Discharge
v. Waivers
5. Alerts
a. Main page
i. List of all Alert posts
1. Include post TITLE as a link to the post
ii. Side Navigation
1. Alerts Archive
a. shown as Month + Number of posts
iii. Alerts > [Alert page]
1. Include TITLE, DATE, AUTHOR, BODY
6. Contact Us
a. Map
b. Hours of operation
c. Address
d. Phone number
e. Fax number
e. Fax number
f. Map
g. Email

Design notes:
- fixed width
- responsive (need designs for mobile, tablet, and desktop)
- simple, dark font, white background
- use Font Awesome icons where needed
- user adds own logo

Target Market(s)

Medical Clinics

Industry/Entity Type

Medical

Number of Pages Required

5+ page

Font styles to use
Serif
Sans Serif

Requirements
Must have
• Please keep designs very simple.
• Examples:
• https://www.quolbin.com/install
• http://www.ventrohax.com/company/about-us
• http://brindlequota.org/
• http://www.trosk.com/
Should not have
• Minimal or no use of shadows and gradients

```html
<!DOCTYPE html>
<html lang="en">
<head>
<meta charset="utf-8">
<title>Clinic Name – Quality Care</title>
<link href="https://fonts.googleapis.com/css2?family=Roboto:wght@300;400;500;700&family=Playball&display=swap" rel="stylesheet">
<style>
:root{
  --blue:#4fb3ee;
  --blue-dark:#1a7fd2;
  --blue-mid:#2a93e3;
  --blue-deep:#156fc6;
  --ink:#333;
  --muted:#666;
  --line:#e3e3e3;
  --soft:#f7f8f9;
  --white:#fff;
}
*{box-sizing:border-box;margin:0;padding:0}
html,body{width:1200px;height:2246px;overflow:hidden}
body{position:relative;background:var(--white);font-family:'Roboto',Arial,sans-serif;color:var(--ink)}
.abs{position:absolute}
a{color:inherit;text-decoration:none}

.topbar{left:0;top:0;width:1200px;height:37px;border-bottom:1px solid var(--line);font-size:11px;color:#888}
.topbar span{position:absolute;top:12px;display:flex;align-items:center;gap:6px;white-space:nowrap}
.topbar .sep{position:absolute;top:0;width:1px;height:37px;background:var(--line)}

.header{left:0;top:37px;width:1200px;height:71px}
.brand{left:125px;top:20px;font-size:26px;font-weight:700;color:#222;display:flex;align-items:center;gap:10px}
.brand i{display:block;width:14px;height:14px;border-radius:50%;background:var(--blue)}
.nav{left:519px;top:0;height:71px;display:flex;font-size:11px;font-weight:500;color:#555}
.nav a{height:71px;display:flex;align-items:center;padding:0 22px}
.nav a.active{background:var(--blue);color:#fff}
.nav a.contact{color:var(--blue)}

.hero{left:0;top:108px;width:1200px;height:343px;background:linear-gradient(90deg,#dbe7ee,#eef4f7 45%,#e4eef3)}
.hero .person{position:absolute;left:200px;top:15px;width:290px;height:328px;background:linear-gradient(180deg,#e9eef1,#cfd9df);border-radius:140px 140px 0 0}
.hero h1{position:absolute;left:517px;top:28px;font-family:'Playball',cursive;font-weight:400;font-size:64px;color:#111}
.hero h2{position:absolute;left:515px;top:118px;font-weight:300;font-size:44px;color:var(--blue-dark)}
.hero .rule{position:absolute;left:517px;top:180px;width:470px;height:1px;background:#9fb6c4}
.hero p{position:absolute;left:517px;top:196px;width:480px;font-size:13px;line-height:19px;color:#222}
.hero .btn{position:absolute;left:518px;top:246px;width:180px;height:45px;background:var(--blue);color:#fff;font-size:15px;display:flex;align-items:center;justify-content:center}
.hero .arrow{position:absolute;top:147px;width:50px;height:50px;border-radius:50%;background:rgba(60,60,60,.7);border:3px solid #ddd;display:flex;align-items:center;justify-content:center}
.hero .dots{position:absolute;left:582px;top:320px;display:flex;gap:4px}
.hero .dots i{width:8px;height:8px;border-radius:50%;border:1px solid #666;background:#fff}
.hero .dots i.on{background:#666}

.infobar{left:110px;top:451px;width:978px;height:238px;display:flex;color:#fff}
.info{width:244.5px;height:238px;padding:22px 22px 0;position:relative;font-size:12px}
.info h3{font-size:17px;font-weight:500;display:flex;justify-content:space-between;align-items:center;height:30px;margin-bottom:12px}
.info .row{display:flex;justify-content:space-between;align-items:center;height:31px;border-bottom:1px solid rgba(255,255,255,.45);white-space:nowrap}
.info .row.plain{border:none}
.info small{display:block;font-size:10px;line-height:14px;margin-top:10px}
.info .btn{position:absolute;left:22px;top:190px;height:31px;padding:0 22px;border:1px solid rgba(255,255,255,.8);background:rgba(0,0,0,.15);font-size:11px;display:flex;align-items:center}
.i1{background:var(--blue)}.i2{background:var(--blue-dark)}.i3{background:var(--blue-mid)}.i4{background:var(--blue-deep)}
.hours .row{border-bottom:1px solid rgba(255,255,255,.35);font-weight:500}
.hours .row b{font-weight:500;width:56px;text-align:right}

.main{left:0;top:689px;width:1200px;height:883px;background:var(--soft)}
.sec-title{font-size:19px;font-weight:400;color:#333;text-transform:uppercase}
.sec-title::after{content:"";display:block;width:110px;height:2px;background:var(--blue);margin-top:10px}

.post{left:125px;width:541px;height:240px;border-bottom:1px solid var(--line)}
.post .date{position:absolute;left:0;top:0;display:flex;height:24px;font-size:10px;color:#fff}
.post .date span{background:var(--blue);padding:0 12px;display:flex;align-items:center}
.post .date b{background:var(--blue-dark);width:34px;display:flex;align-items:center;justify-content:center;font-weight:500}
.post .photo{position:absolute;left:0;top:47px;width:218px;height:172px}
.post h4{position:absolute;left:244px;top:54px;font-size:19px;font-weight:400;color:#333}
.post p{position:absolute;left:244px;top:84px;width:297px;font-size:10px;line-height:14px;color:#666}
.post .more{position:absolute;left:244px;top:165px;width:70px;height:25px;background:var(--blue);color:#fff;font-size:10px;display:flex;align-items:center;justify-content:center}
.post .meta{position:absolute;left:244px;top:206px;font-size:10px;color:#777}
.post .meta a{color:var(--blue);text-decoration:underline}

.acc-head{left:693px;top:786px;width:383px;height:30px;background:var(--blue);color:#fff;font-size:12px;display:flex;align-items:center;justify-content:space-between;padding:0 12px}
.acc-body{left:693px;top:816px;width:383px;height:140px;background:#fff;border-bottom:1px solid var(--line)}
.acc-row{left:693px;width:383px;height:28px;border-bottom:1px solid var(--line);font-size:12px;color:#666;display:flex;align-items:center;justify-content:space-between;padding:0 12px}
.btn-s{height:30px;background:var(--blue);color:#fff;font-size:10px;display:flex;align-items:center;justify-content:center}

.staff-card{top:1660px;width:218px}
.staff-card .photo{height:216px}
.staff-card h5{margin-top:13px;text-align:center;font-size:14px;font-weight:400;color:var(--blue-dark)}
.staff-card p{text-align:center;font-size:11px;color:#555;margin-top:5px}
.staff-card .bar{height:6px;background:var(--blue);margin-top:14px}

.footer{left:0;top:1981px;width:1200px;height:217px;background:var(--blue);color:#fff}
.fcol{position:absolute;top:38px}
.fcol h6{font-size:17px;font-weight:400;margin-bottom:14px}
.fcol li{list-style:none;font-size:11px;height:28px;display:flex;align-items:center;border-bottom:1px solid rgba(255,255,255,.3);width:130px}
.fsep{position:absolute;top:42px;width:1px;height:130px;background:rgba(255,255,255,.35)}
.fhours div{display:flex;font-size:12px;font-weight:500;height:30px;align-items:center;border-bottom:1px solid rgba(255,255,255,.3);width:210px}
.fhours div span{width:80px}
.fcontact div{display:flex;gap:10px;font-size:11px;height:30px;align-items:center;white-space:nowrap}
.copy{left:0;top:2198px;width:1200px;height:48px;display:flex;align-items:center;justify-content:center;font-size:11px;color:#555}
.copy b{color:var(--blue-dark);font-weight:500;margin-left:3px}
</style>
</head>
<body>

<div class="abs topbar">
  <span style="left:125px"><svg width="12" height="12" viewBox="0 0 12 12"><rect x="1" y="3" width="10" height="7" fill="none" stroke="#aaa"/><rect x="4" y="1" width="4" height="2" fill="none" stroke="#aaa"/></svg>Physician Toolbox</span>
  <div class="sep" style="left:257px"></div>
  <span style="left:272px"><svg width="12" height="12" viewBox="0 0 12 12"><circle cx="6" cy="6" r="5" fill="none" stroke="#aaa"/><path d="M6 3v3h2" stroke="#aaa" fill="none"/></svg>Book an Appointment</span>
  <div class="sep" style="left:420px"></div>
  <div class="sep" style="left:695px"></div>
  <span style="left:712px"><svg width="12" height="12" viewBox="0 0 12 12"><rect x="1" y="3" width="10" height="7" fill="none" stroke="#aaa"/><path d="M1 3l5 4 5-4" stroke="#aaa" fill="none"/></svg>Send Mail: mail@orvelcare.net</span>
  <div class="sep" style="left:910px"></div>
  <span style="left:930px"><svg width="12" height="12" viewBox="0 0 12 12"><path d="M3 1l2 3-1 1c1 2 2 3 3 3l1-1 3 2-1 2C5 11 1 7 1 3z" fill="#aaa"/></svg>Call Us: 0800 - 4471 - 26</span>
  <div class="sep" style="left:1076px"></div>
</div>

<header class="abs header">
  <a class="abs brand" href="#"><i></i>Clinic Name</a>
  <nav class="abs nav">
    <a class="active" href="#">HOME</a><a href="#">OUR CLINIC</a><a href="#">STAFF</a><a href="#">RESOURCES</a><a href="#">ALERTS</a><a class="contact" href="#">CONTACT US</a>
  </nav>
</header>

<section class="abs hero">
  <div class="person" role="img" aria-label="Photo of a doctor in a white coat holding a tablet in a bright clinic"></div>
  <h1>Quality Care !</h1>
  <h2>Provided For everyone...</h2>
  <div class="rule"></div>
  <p>Highly skilled and Experienced medical staff comfortable and cosy patient rooms,state-of-theart dianostic equipment</p>
  <a class="btn" href="#">Book an Appointment</a>
  <div class="arrow" style="left:125px"><svg width="14" height="14" viewBox="0 0 14 14"><path d="M9 2L4 7l5 5" stroke="#fff" stroke-width="2" fill="none"/></svg></div>
  <div class="arrow" style="left:1023px"><svg width="14" height="14" viewBox="0 0 14 14"><path d="M5 2l5 5-5 5" stroke="#fff" stroke-width="2" fill="none"/></svg></div>
  <div class="dots"><i class="on"></i><i></i><i></i></div>
</section>

<section class="abs infobar">
  <div class="info i1">
    <h3>NEW PATIENTS <svg width="22" height="22" viewBox="0 0 22 22"><circle cx="9" cy="3" r="2" fill="#fff"/><path d="M9 6v6h6l3 6M9 9a6 6 0 1 0 6 8" stroke="#fff" stroke-width="2" fill="none"/></svg></h3>
    <div class="row">Accepting New Patients <span>→</span></div>
    <small>Lorem ipsum dolor sit amet, consectetuer adipiscing elit,sed diam nonummy nibh euismod tincidunt ut laoreet dolore magna aliquam erat volutpat. Ut wisi enim ad minim veniam, quis nostrud exerci tation.</small>
    <a class="btn" href="#">CONTACT US</a>
  </div>
  <div class="info i2">
    <h3>USEFULL LINKS <svg width="22" height="22" viewBox="0 0 22 22"><path d="M9 13l4-4M7 11l-3 3a3 3 0 0 0 4 4l3-3M15 11l3-3a3 3 0 0 0-4-4l-3 3" stroke="#fff" stroke-width="2" fill="none"/></svg></h3>
    <div class="row">LTF Clinics <span>→</span></div>
    <div class="row">LTF Clinics <span>→</span></div>
    <div class="row">LTF Clinics <span>→</span></div>
    <div class="row">LTF Clinics <span>→</span></div>
    <a class="btn" href="#">MORE LINKS</a>
  </div>
  <div class="info i3">
    <h3>CONTACT INFO <svg width="26" height="20" viewBox="0 0 26 20"><path d="M6 17a5 5 0 0 1 0-10 7 7 0 0 1 13 0 5 5 0 0 1 1 10z" fill="#fff"/></svg></h3>
    <div class="row">☏ Phone <span>804-370-2168</span></div>
    <div class="row">✉ Email <span>desk@orvelcare.net</span></div>
    <div class="row plain" style="align-items:flex-start;padding-top:8px;height:50px">⌖ Address <span style="text-align:right;font-size:11px;line-height:14px">48 Tamber Road,<br>Elsfield, B.C<br>Canada. x2p 7kd</span></div>
    <a class="btn" href="#">MORE INFO</a>
  </div>
  <div class="info i4 hours">
    <h3>OPENING HOURS <svg width="22" height="22" viewBox="0 0 22 22"><rect x="2" y="4" width="18" height="16" fill="none" stroke="#fff" stroke-width="2"/><path d="M2 9h18M7 2v4M15 2v4" stroke="#fff" stroke-width="2"/></svg></h3>
    <div class="row">Mon - Fri <b>8:00 AM</b> - <b>6:00 PM</b></div>
    <div class="row">Saturday <b>9:00 AM</b> - <b>4:00 PM</b></div>
    <div class="row">Sunday <b>9:00 AM</b> - <b>4:00 PM</b></div>
    <div class="row plain"><u>Holiday Hours !</u></div>
    <a class="btn" href="#">APPOINTMENT</a>
  </div>
</section>

<section class="abs main"></section>

<h2 class="abs sec-title" style="left:125px;top:733px">Latest Alerts</h2>

<article class="abs post" style="top:788px">
  <div class="date"><span>JUNE 2015</span><b>12</b></div>
  <div class="photo" role="img" aria-label="Photo of a medical team seated at a meeting table" style="background:linear-gradient(135deg,#eef2f5,#c9d6df)"></div>
  <h4>LOREM IPSUM DOLOR SIT AMET !</h4>
  <p>Lorem ipsum dolor sit amet, consectetuer adipiscing, sed diam nonummy nibh euismod tincidunt ut laoreet dolore magna aliquam erat volutpat. Ut wisi enim ad minim veniam, quis nostrud exerci tation ullamcorper suscipit lobortis nisl ut aliquip ex ea commodo conat...</p>
  <a class="more" href="#">More</a>
  <div class="meta">Posted in <a href="#">General</a>, <a href="#">Clinic Name</a></div>
</article>

<article class="abs post" style="top:1043px">
  <div class="date"><span>JUNE 2015</span><b>12</b></div>
  <div class="photo" role="img" aria-label="Photo of a doctor consulting with a patient at a desk" style="background:linear-gradient(135deg,#e9ecef,#c3ccd3)"></div>
  <h4>LOREM IPSUM DOLOR SIT AMET !</h4>
  <p>Lorem ipsum dolor sit amet, consectetuer adipiscing, sed diam nonummy nibh euismod tincidunt ut laoreet dolore magna aliquam erat volutpat. Ut wisi enim ads minim veniam, quis nostrud exerci tation ullamcorper suscipit lobortis nisl ut aliquip ex ea commodo conat...</p>
  <a class="more" href="#">More</a>
  <div class="meta">Posted in <a href="#">General</a>, <a href="#">Clinic Name</a></div>
</article>

<article class="abs post" style="top:1292px;border-bottom:none">
  <div class="date"><span>JUNE 2015</span><b>12</b></div>
  <div class="photo" role="img" aria-label="Photo of a group of smiling medical staff" style="background:linear-gradient(135deg,#f0f3f5,#bccbd6)"></div>
  <h4>LOREM IPSUM DOLOR SIT AMET !</h4>
  <p>Lorem ipsum dolor sit amet, consectetuer adipiscing, sed diam nonummy nibh euismod tincidunt ut laoreet dolore magna aliquam erat volutpat. Ut wisi enim ads minim veniam, quis nostrud exerci tation ullamcorper suscipit lobortis nisl ut aliquip ex ea commodo conat...</p>
  <a class="more" href="#">More</a>
  <div class="meta">Posted in <a href="#">General</a>, <a href="#">Clinic Name</a></div>
</article>

<h2 class="abs sec-title" style="left:693px;top:726px">Clinic Policies !</h2>
<div class="abs acc-head">Late Arrivals ! <span style="font-size:18px">—</span></div>
<div class="abs acc-body">
  <div class="abs" role="img" aria-label="Photo of a nurse caring for an elderly patient" style="left:4px;top:21px;width:114px;height:105px;background:linear-gradient(135deg,#e6ebee,#c4cfd6)"></div>
  <p class="abs" style="left:130px;top:28px;width:250px;font-size:10px;line-height:14px;color:#666">Lorem ipsum dolor sit amet, consectetuer adipiscing, sed diam nonummy nibh euismod tincidunt ut laoreet dolore magna aliquam erat volutpat. Ut wisi enim ads minim veniam, quis nostrud exerci tation ullamcorper suscipit lobortis nisl ut aliquip ex ea commodo conat.</p>
  <a class="abs btn-s" href="#" style="left:130px;top:101px;width:70px;height:25px">More</a>
</div>
<div class="abs acc-row" style="top:956px">Missed Appointments <span style="font-size:18px">+</span></div>
<div class="abs acc-row" style="top:984px">Fees For Missed Appointments <span style="font-size:18px">+</span></div>
<a class="abs btn-s" href="#" style="left:693px;top:1026px;width:96px">VIEW MORE</a>

<h2 class="abs sec-title" style="left:693px;top:1081px">Our Clinic !</h2>
<div class="abs" role="img" aria-label="Photo of a doctor working in a clinic laboratory" style="left:693px;top:1131px;width:383px;height:196px;background:linear-gradient(135deg,#eef1f3,#b9c8d6 60%,#3f7fc8)"></div>
<h3 class="abs" style="left:693px;top:1347px;font-size:18px;font-weight:400;color:var(--blue)">LOREM IPSUM DOLOR SIT AMET !</h3>
<p class="abs" style="left:693px;top:1385px;width:383px;font-size:10px;line-height:14px;color:#666">Lorem ipsum dolor sit amet, consectetuer adipiscing, sed diam nonummy nibh euismod tincidunt ut laoreet dolore magna sadx aliquam erat volutpat. Ut wisi enim ads minim veniam, quis nostrud exerci tation ullamcorper suscipit lobortis nisl ut aliquip ex ea commodo conat adx aliquam erat volutpat. Ut wisi enim ads minim veniam, quis nostrud exercixadx aliquam erat volutpat. Ut wisi enim ads minim veniam, quis nostrud exerci.</p>
<div class="abs" style="left:693px;top:1474px;width:280px;height:1px;background:var(--line)"></div>
<a class="abs btn-s" href="#" style="left:693px;top:1483px;width:70px;height:26px">More</a>

<h2 class="abs sec-title" style="left:125px;top:1604px">Our Staff !</h2>
<div class="abs" style="left:1009px;top:1605px;width:29px;height:29px;border:1px solid #bbb;display:flex;align-items:center;justify-content:center"><svg width="10" height="10" viewBox="0 0 10 10"><path d="M7 1L3 5l4 4" stroke="#777" fill="none" stroke-width="1.5"/></svg></div>
<div class="abs" style="left:1046px;top:1605px;width:29px;height:29px;border:1px solid #bbb;display:flex;align-items:center;justify-content:center"><svg width="10" height="10" viewBox="0 0 10 10"><path d="M3 1l4 4-4 4" stroke="#777" fill="none" stroke-width="1.5"/></svg></div>

<div class="abs staff-card" style="left:125px">
  <div class="photo" role="img" aria-label="Photo of a smiling doctor with medical staff behind" style="background:linear-gradient(135deg,#eef2f5,#c2d3df)"></div>
  <h5>Dr. John Smith. MD</h5><p>Surgon</p><div class="bar"></div>
</div>
<div class="abs staff-card" style="left:369px">
  <div class="photo" role="img" aria-label="Staff member photo under a blue overlay" style="background:linear-gradient(135deg,#5fbcf0,#3a9fe2);position:relative">
    <div style="position:absolute;left:108px;top:58px;width:1px;height:60px;background:rgba(255,255,255,.6)"></div>
    <div style="position:absolute;left:78px;top:88px;width:60px;height:1px;background:rgba(255,255,255,.6)"></div>
    <div style="position:absolute;left:68px;top:142px;width:34px;height:34px;border:1px solid #fff"></div>
    <div style="position:absolute;left:110px;top:142px;width:34px;height:34px;border:1px solid #fff"></div>
  </div>
  <h5>Dr. John Smith. MD</h5><p>Surgon</p><div class="bar"></div>
</div>
<div class="abs staff-card" style="left:612px">
  <div class="photo" role="img" aria-label="Photo of a female doctor using a tablet" style="background:linear-gradient(135deg,#f3f4f5,#d2d9de)"></div>
  <h5>Dr. John Smith. MD</h5><p>Surgon</p><div class="bar"></div>
</div>
<div class="abs staff-card" style="left:855px">
  <div class="photo" role="img" aria-label="Photo of a nurse in teal scrubs holding a clipboard" style="background:linear-gradient(135deg,#e8eef1,#8fc7c9)"></div>
  <h5>Dr. John Smith. MD</h5><p>Surgon</p><div class="bar"></div>
</div>

<footer class="abs footer">
  <div class="fcol" style="left:144px"><h6>Our Clinic</h6><ul><li>Mission</li><li>Services</li><li>Schedules</li><li>Policies</li></ul></div>
  <div class="fsep" style="left:318px"></div>
  <div class="fcol" style="left:361px"><h6>Resources</h6><ul><li>Our clinic</li><li>Mission</li><li>Services</li></ul></div>
  <div class="fsep" style="left:535px"></div>
  <div class="fcol fhours" style="left:578px"><h6>Hours of operation</h6>
    <div><span>Mon - Fri</span>8:00 AM &nbsp;-&nbsp; 6:00 PM</div>
    <div><span>Saturday</span>9:00 AM &nbsp;-&nbsp; 4:00 PM</div>
    <div><span>Sunday</span>9:00 AM &nbsp;-&nbsp; 4:00 PM</div>
    <div style="border:none"><u>Holiday Hours !</u></div>
  </div>
  <div class="fsep" style="left:830px"></div>
  <div class="fcol fcontact" style="left:865px"><h6>Contact us</h6>
    <div><svg width="12" height="12" viewBox="0 0 12 12"><path d="M3 1l2 3-1 1c1 2 2 3 3 3l1-1 3 2-1 2C5 11 1 7 1 3z" fill="#fff"/></svg>123-409-618</div>
    <div><svg width="12" height="12" viewBox="0 0 12 12"><rect x="1" y="3" width="10" height="7" fill="#fff"/><path d="M1 3l5 4 5-4" stroke="#4fb3ee" fill="none"/></svg>hello@orvelcare.net</div>
    <div><svg width="12" height="12" viewBox="0 0 12 12"><path d="M6 11C3 7 2 5.5 2 4.5a4 4 0 0 1 8 0C10 5.5 9 7 6 11z" fill="#fff"/><circle cx="6" cy="4.5" r="1.5" fill="#4fb3ee"/></svg>57 Quarry Lane , Mossby,K.t</div>
  </div>
</footer>
<div class="abs copy">© 2015 Copyright <b>OrvelCare.net</b></div>

</body>
</html>
```